BOLD & MINIMALIST DESIGN NEEDED

We want a very bold but minimalistic business card design that is impactful and utilizes both sides of the business card. Our current logo is included for your use.

We want bold fonts and good use of negative space. We don't want the logo to overpower the design.

Target Market(s)

Professionals who are building new commercial buildings.

Industry/Entity Type

Construction

Contact Information for Business Card

Name, Title, email, office phone, cell phone, website

Font styles to use
Serif
Sans Serif

Requirements
Must have
• Bold design!

```html
<!DOCTYPE html>
<html lang="en">
<head>
<meta charset="utf-8">
<title>Ridgeline Build – Business Cards</title>
<link rel="stylesheet" href="https://fonts.googleapis.com/css2?family=Poppins:wght@400;500;700;800&display=swap">
<style>
  :root {
    --backdrop: #2a2a2a;
    --card-dark: #0d0d0f;
    --card-light: #ffffff;
    --ink: #111111;
    --green: #7dc242;
    --muted: #444444;
  }
  * { margin: 0; padding: 0; box-sizing: border-box; }
  html, body { width: 1200px; height: 880px; overflow: hidden; }
  body {
    background: var(--backdrop);
    font-family: "Poppins", sans-serif;
    position: relative;
  }
  .card {
    position: absolute;
    width: 560px;
    height: 320px;
    border-radius: 18px;
    overflow: hidden;
  }
  /* Back side */
  .card-back {
    left: 70px;
    top: 70px;
    background: var(--card-dark);
    color: #fff;
    display: flex;
    flex-direction: column;
    align-items: center;
    justify-content: center;
    gap: 34px;
  }
  .brand {
    display: flex;
    align-items: center;
    gap: 12px;
    font-weight: 800;
    font-size: 40px;
    letter-spacing: 0.5px;
    line-height: 1;
    white-space: nowrap;
  }
  .brand-mark {
    width: 22px;
    height: 22px;
    background: var(--green);
  }
  .card-back .brand { color: #fff; }
  .back-web {
    font-size: 15px;
    letter-spacing: 5px;
    font-weight: 500;
  }
  /* Front side */
  .card-front {
    left: 570px;
    top: 500px;
    background: var(--card-light);
    color: var(--ink);
  }
  .card-front .brand {
    position: absolute;
    right: 36px;
    top: 48px;
    font-size: 32px;
    color: var(--ink);
  }
  .rule-top {
    position: absolute;
    left: 250px;
    right: 36px;
    top: 118px;
    height: 1.5px;
    background: var(--green);
  }
  .person {
    position: absolute;
    left: 40px;
    top: 150px;
  }
  .person-name {
    font-weight: 700;
    font-size: 22px;
    letter-spacing: 0.5px;
    line-height: 1.1;
  }
  .person-title {
    font-size: 16px;
    color: var(--green);
    line-height: 1.3;
  }
  .rule-contact {
    position: absolute;
    left: 40px;
    width: 250px;
    top: 215px;
    height: 1.5px;
    background: var(--green);
  }
  .contact-list {
    position: absolute;
    left: 40px;
    top: 228px;
    list-style: none;
    font-size: 15px;
    color: var(--muted);
  }
  .contact-list li {
    display: flex;
    align-items: center;
    gap: 10px;
    height: 26px;
    white-space: nowrap;
  }
  .contact-icon {
    width: 18px;
    height: 18px;
    flex: none;
  }
  .web-tab {
    position: absolute;
    right: 0;
    bottom: 0;
    width: 260px;
    height: 58px;
    background: var(--green);
    border-top-left-radius: 40px;
    color: #fff;
    font-size: 15px;
    font-weight: 500;
    display: flex;
    align-items: center;
    justify-content: center;
    white-space: nowrap;
  }
</style>
</head>
<body>
  <section class="card card-back" aria-label="Business card back">
    <div class="brand"><span class="brand-mark"></span>Ridgeline Build</div>
    <p class="back-web">www.ridgelinebuild.com</p>
  </section>

  <section class="card card-front" aria-label="Business card front">
    <div class="brand"><span class="brand-mark"></span>Ridgeline Build</div>
    <div class="rule-top"></div>
    <div class="person">
      <p class="person-name">MARCUS ELLERY</p>
      <p class="person-title">Manager</p>
    </div>
    <div class="rule-contact"></div>
    <ul class="contact-list">
      <li>
        <svg class="contact-icon" viewBox="0 0 20 20" aria-hidden="true">
          <circle cx="10" cy="10" r="10" fill="#7dc242"/>
          <path d="M7 5.5l1.6 2.6-1 1c.6 1.3 1.6 2.3 2.9 2.9l1-1 2.6 1.6-.7 1.6c-3.8-.3-6.7-3.2-7-7z" fill="#fff"/>
        </svg>
        (555) 210-4817
      </li>
      <li>
        <svg class="contact-icon" viewBox="0 0 20 20" aria-hidden="true">
          <circle cx="10" cy="10" r="10" fill="#7dc242"/>
          <rect x="5" y="6.5" width="10" height="7" fill="#fff"/>
          <path d="M5 6.5l5 4 5-4" fill="none" stroke="#7dc242" stroke-width="1.2"/>
        </svg>
        info@ridgelinebuild.com
      </li>
    </ul>
    <div class="web-tab">www.ridgelinebuild.com</div>
  </section>
</body>
</html>
```